Shopify Web-Page "Tiny-ThreadDays

We are building a new business in Switzerland offering premium sewing holiday camps for kids aged 9–14. In enclosed brief outlines our requirements for a complete Shopify homepage design and a multilingual logo creation.
Domains: tiny-threaddays.ch ; tiny-giornifilo.ch ; tiny-fadentage.ch

Project Overview
We are looking for:
1. A modern, fully designed Shopify homepage in English using standard Shopify content blocks (no custom coding), which we can later update ourselves. Supporting Multilanguage (EN, German, Italian).

2. A logo design that includes the brand identity and communicates our multilingual, creative, and child-focused positioning.

All details in enclosed

```html
<!DOCTYPE html>
<html lang="en">
<head>
<meta charset="utf-8">
<title>Tiny-ThreadDays – Sewing Holiday Camps</title>
<link href="https://fonts.googleapis.com/css2?family=Signika:wght@400;500;600&family=Open+Sans:wght@400;600&display=swap" rel="stylesheet">
<style>
:root{
  --coral:#f5866f;
  --teal:#3fa7a1;
  --ink:#1d1d1d;
  --muted:#6b6b6b;
  --footer:#0c0c0c;
  --white:#ffffff;
}
*{box-sizing:border-box;margin:0;padding:0}
html,body{width:1200px;height:4239px;overflow:hidden;background:var(--white)}
body{position:relative;font-family:"Open Sans",sans-serif;color:var(--ink)}
.abs{position:absolute}
h1,h2,h3{font-family:"Signika",sans-serif;font-weight:400}
.accent{color:var(--teal);font-weight:500}
.btn{position:absolute;display:flex;align-items:center;justify-content:center;border-radius:30px;color:#fff;font-family:"Signika",sans-serif;font-weight:500;white-space:nowrap}
.btn.coral{background:var(--coral)}
.btn.teal{background:var(--teal)}
.photo{position:absolute;overflow:hidden}

/* header */
.topline{left:0;top:0;width:1200px;height:5px;background:var(--teal)}
.header{left:0;top:5px;width:1200px;height:115px;background:#fff;border-bottom:1px solid #e8e8e8}
.brand{left:110px;top:45px;font-family:"Signika",sans-serif;font-weight:600;font-size:22px;color:var(--teal);display:flex;align-items:center;gap:8px;white-space:nowrap}
.brand .dot{width:12px;height:12px;border-radius:50%;background:var(--coral)}
.nav{left:316px;top:52px;display:flex;font-size:14px;white-space:nowrap}
.nav a{color:var(--ink);text-decoration:none;position:relative}
.nav a.active{color:var(--coral);font-weight:600}
.nav a.active::after{content:"";position:absolute;left:-8px;right:-8px;top:62px;height:4px;background:var(--coral)}
.nav-icons{left:998px;top:53px;display:flex;gap:10px}

/* hero */
.hero{left:0;top:120px;width:1200px;height:634px;background:linear-gradient(180deg,#b07a86 0%,#a37a7d 45%,#8a6b73 100%)}
.hero-title{left:0;top:318px;width:1200px;text-align:center;color:#fff;font-family:"Signika",sans-serif;font-weight:600;font-size:60px;text-shadow:0 2px 6px rgba(0,0,0,.35)}
.hero-sub{left:0;top:394px;width:1200px;text-align:center;color:#fff;font-weight:600;font-size:22px;text-shadow:0 1px 4px rgba(0,0,0,.4)}

/* about */
.about-title{left:642px;top:858px;font-size:44px}
.about-text{left:642px;top:930px;width:444px;font-size:13.5px;line-height:25px;color:#555;text-align:justify}
.about-text p{margin-bottom:13px}

.section-title{left:0;width:1200px;text-align:center;font-size:44px}

/* steps */
.steps{left:100px;top:1560px;width:1000px;display:flex}
.step{width:200px;text-align:center}
.step svg{display:block;margin:0 auto 22px;height:58px}
.step h3{font-size:20px;font-weight:500;margin-bottom:14px;white-space:nowrap}
.step p{font-size:13.5px;line-height:25px;color:#666;padding:0 12px}

/* bands */
.band{left:110px;width:978px;height:418px;border-radius:22px;overflow:hidden;display:flex}
.band .side{width:316px;height:100%}
.band .mid{width:346px;height:100%;text-align:center;color:#fff;position:relative}
.band h2{font-size:44px;font-weight:500;line-height:54px}

/* camps */
.camp{position:absolute;top:2535px;width:490px;height:240px}
.camp .img{position:absolute;left:0;top:0;width:231px;height:238px;border-radius:4px}
.camp .date{position:absolute;left:16px;top:196px;background:#fff;border-radius:18px;padding:6px 14px;font-size:14px;font-weight:600;white-space:nowrap}
.camp h3{position:absolute;left:263px;top:8px;font-size:24px;font-weight:500;white-space:nowrap}
.camp p{position:absolute;left:263px;top:58px;width:208px;font-size:12.5px;line-height:25px;color:#666}
.camp .btn{left:263px;top:198px;width:104px;height:36px;font-size:13px}

/* reasons */
.reasons{left:100px;top:3068px;width:1000px;display:flex}
.reason{width:171px;text-align:center}
.reason svg{display:block;margin:0 auto 22px;height:50px}
.reason p{font-size:13.5px;line-height:24px;color:#666;padding:0 6px}

/* footer */
.footer{left:0;top:3861px;width:1200px;height:378px;background:var(--footer)}
.f-brand{left:112px;top:3950px;font-family:"Signika",sans-serif;font-weight:600;font-size:28px;color:var(--teal);display:flex;align-items:center;gap:10px;white-space:nowrap}
.f-brand .dot{width:14px;height:14px;border-radius:50%;background:var(--coral)}
.socials{left:110px;top:4058px;display:flex;gap:6px}
.socials span{width:30px;height:30px;border-radius:50%;background:#fff;display:block}
.socials span:first-child{background:var(--teal)}
.f-head{font-family:"Signika",sans-serif;font-weight:500;font-size:21px;color:var(--coral);white-space:nowrap}
.links{left:397px;top:3990px;font-size:14px;line-height:27.5px;color:var(--white)}
.contact-row{position:absolute;left:584px;display:flex;align-items:center;gap:14px;font-size:14px;color:var(--white);white-space:nowrap}
.news-text{left:857px;top:3986px;width:230px;font-size:11.5px;line-height:21px;text-align:justify;color:var(--white)}
.email-field{left:857px;top:4068px;width:232px;height:40px;border:2px solid #fff;border-radius:22px;font-size:13px;padding:10px 18px;color:var(--white)}
.rule{left:110px;top:4194px;width:980px;height:1px;background:#888}
.copy{left:0;top:4208px;width:1200px;text-align:center;font-size:13px;color:var(--white)}
</style>
</head>
<body>

<div class="abs topline"></div>
<header class="abs header"></header>
<div class="abs brand"><span>Tiny-ThreadDays</span><span class="dot"></span></div>
<nav class="abs nav">
  <a class="active" href="#" style="margin-right:34px">Home</a>
  <a href="#" style="margin-right:34px">About Us</a>
  <a href="#" style="margin-right:34px">Camp</a>
  <a href="#" style="margin-right:34px">How It Works</a>
  <a href="#" style="margin-right:38px">Why Choose Us</a>
  <a href="#" style="margin-right:34px">Blog</a>
  <a href="#">Contac Us</a>
</nav>
<div class="abs nav-icons">
  <svg width="20" height="20" viewBox="0 0 20 20" fill="none" stroke="#222" stroke-width="1.8"><circle cx="8.5" cy="8.5" r="6.5"/><path d="M13.5 13.5l5 5"/></svg>
  <svg width="24" height="20" viewBox="0 0 24 20" fill="none" stroke="#222" stroke-width="1.8"><path d="M1 2h4l3 11h12l2-8H7"/><circle cx="9" cy="17" r="1.6"/><circle cx="18" cy="17" r="1.6"/></svg>
  <svg width="18" height="20" viewBox="0 0 18 20" fill="none" stroke="#222" stroke-width="1.8"><circle cx="9" cy="6" r="4.5"/><path d="M1.5 19c0-4.5 3.3-7 7.5-7s7.5 2.5 7.5 7z"/></svg>
</div>

<section class="abs hero" role="img" aria-label="Children and an instructor sewing together at a craft table"></section>
<h1 class="abs hero-title">Where Creativity Meets Adventure!</h1>
<p class="abs hero-sub">Discover Switzerland's most inspiring sewing holiday camps for kids aged 9–14</p>
<div class="btn coral" style="left:407px;top:447px;width:161px;height:48px;font-size:17px">Register Now</div>
<div class="btn teal" style="left:579px;top:447px;width:214px;height:48px;font-size:17px">Discover Our Camps</div>

<!-- about -->
<div class="photo" role="img" aria-label="Girls threading yarn at a workshop table with an instructor" style="left:110px;top:866px;width:443px;height:345px;border-radius:12px;background:linear-gradient(135deg,#a9b48d,#c9a98f 55%,#7f9aa5)"></div>
<div class="photo" role="img" aria-label="Portrait of instructor Lena" style="left:110px;top:1241px;width:143px;height:117px;border-radius:10px;background:linear-gradient(135deg,#7b8a5f,#5e6b46)"></div>
<div class="photo" role="img" aria-label="Portrait of instructor Mara" style="left:263px;top:1241px;width:142px;height:117px;border-radius:10px;background:linear-gradient(135deg,#e9e9e9,#bdbdbd)"></div>
<div class="photo" role="img" aria-label="Portrait of a camp team member" style="left:420px;top:1241px;width:142px;height:117px;border-radius:10px;background:linear-gradient(135deg,#c7c2b4,#8e8a6e)"></div>

<h2 class="abs about-title">About <span class="accent">Us</span></h2>
<div class="abs about-text">
  <p>Lena and Mara have over 10 years of experience in teaching children sewing, tailoring, and design with fun, style, and structure.</p>
  <p>In small groups (max. 8 children), we guide young talents through a creative week of vacation – with real results: self-sewn pieces, new friends, and lots of pride.</p>
  <p>At the last day, the children show off their success, their own sewn unique pieces, in a symapatic fashion show.</p>
  <p>Our camps are designed to help kids learn new skills, make lasting friendships, and express their individuality through sewing, design, and creative projects. Each program is guided by experienced instructors who nurture confidence and teamwork in a safe, inclusive environment.</p>
</div>
<div class="btn coral" style="left:639px;top:1291px;width:135px;height:48px;font-size:17px">Read More</div>

<!-- how it works -->
<h2 class="abs section-title" style="top:1458px">How The <span class="accent">Camp Works</span></h2>
<div class="abs steps">
  <div class="step">
    <svg viewBox="0 0 50 58" width="50"><rect x="14" y="4" width="28" height="38" rx="2" fill="#555"/><path d="M19 12h18M19 18h18M19 24h12" stroke="#fff" stroke-width="2"/><circle cx="14" cy="46" r="6" fill="none" stroke="#555" stroke-width="3"/><rect x="2" y="50" width="8" height="4" fill="#555"/></svg>
    <h3>Project selection</h3>
    <p>Your child chooses their own model based on previously produced clothing items and sewing patterns.</p>
  </div>
  <div class="step">
    <svg viewBox="0 0 56 58" width="56"><rect x="4" y="4" width="16" height="50" rx="8" fill="#777"/><circle cx="12" cy="40" r="6" fill="#fff"/><circle cx="12" cy="40" r="2.5" fill="#777"/><rect x="20" y="22" width="32" height="32" fill="#555"/></svg>
    <h3>Fabric selection</h3>
    <p>High-quality fabrics are available.</p>
  </div>
  <div class="step">
    <svg viewBox="0 0 54 58" width="54"><path d="M6 20h34v12H20v18H6z" fill="#555"/><rect x="34" y="10" width="12" height="40" fill="#555"/><rect x="2" y="50" width="50" height="6" fill="#555"/><circle cx="40" cy="22" r="3" fill="#fff"/></svg>
    <h3>Sewing machine</h3>
    <p>operation – Learn how to use a sewing machine</p>
  </div>
  <div class="step">
    <svg viewBox="0 0 50 58" width="50" fill="none" stroke="#555" stroke-width="2.5"><path d="M6 14h38M6 29h38M6 44h38"/><circle cx="16" cy="14" r="5" fill="#fff"/><circle cx="34" cy="29" r="5" fill="#fff"/><circle cx="20" cy="44" r="5" fill="#fff"/></svg>
    <h3>Sewing &amp; refining</h3>
    <p>Step by step to the goal with professional guidance</p>
  </div>
  <div class="step">
    <svg viewBox="0 0 50 58" width="50"><rect x="6" y="8" width="38" height="38" fill="none" stroke="#555" stroke-width="3"/><path d="M25 16l3.5 7.5 8 1-6 5.5 1.5 8-7-4-7 4 1.5-8-6-5.5 8-1z" fill="#555"/><rect x="2" y="4" width="46" height="5" fill="#555"/></svg>
    <h3>Showtime!</h3>
    <p>Fashion show or photo shoot at the end of the week</p>
  </div>
</div>

<!-- cta band -->
<section class="abs band" style="top:1914px">
  <div class="side" role="img" aria-label="Girl knitting blue yarn at a craft table" style="background:linear-gradient(135deg,#8f7d66,#b9a48a 60%,#5f6f6c)"></div>
  <div class="mid" style="background:var(--coral)">
    <h2 style="position:absolute;left:0;width:100%;top:38px">Ready to<br>Stitch Some<br>Memories?</h2>
    <p style="position:absolute;left:46px;width:254px;top:214px;font-size:12.5px;line-height:24px">Each program includes hands-on sewing projects, guided instruction, and a safe, multilingual environment that encourages learning and self-expression.</p>
    <div class="btn teal" style="left:103px;top:324px;width:142px;height:40px;font-size:15px">Register Now</div>
  </div>
  <div class="side" role="img" aria-label="Children cutting fabric with an instructor in a bright studio" style="background:linear-gradient(135deg,#dcdcd8,#b7b5ad 60%,#8a8780)"></div>
</section>

<!-- upcoming camps -->
<h2 class="abs section-title" style="top:2422px">Upcoming <span class="accent">Camps</span></h2>
<div class="camp" style="left:112px">
  <div class="img" role="img" aria-label="Kids working at sewing tables in a summer workshop" style="background:linear-gradient(135deg,#8c8f7a,#c7c1b2 55%,#5a5a55)"></div>
  <span class="date">July 7–12, 2025</span>
  <h3>Summer Camps</h3>
  <p>Children will design and create their own summer accessories — from tote bags to custom t-shirts — while exploring color, fabric, and pattern.</p>
  <div class="btn coral">Read More</div>
</div>
<div class="camp" style="left:635px">
  <div class="img" role="img" aria-label="Children using sewing machines in a spring workshop" style="background:linear-gradient(135deg,#d9d7d2,#a9a39b 55%,#6d6862)"></div>
  <span class="date">July 7–12, 2025</span>
  <h3 style="left:260px">Spring Camps</h3>
  <p style="left:260px">Children will design and create their own spring accessories — from tote bags to custom t-shirts — while exploring color, fabric, and pattern.</p>
  <div class="btn coral" style="left:260px">Read More</div>
</div>
<svg class="abs" style="left:568px;top:2833px" width="64" height="24" viewBox="0 0 64 24"><circle cx="12" cy="12" r="11" fill="#3fa7a1"/><path d="M14 7l-5 5 5 5" stroke="#fff" stroke-width="2.2" fill="none"/><circle cx="45" cy="12" r="11" fill="#c9c9c9"/><path d="M43 7l5 5-5 5" stroke="#fff" stroke-width="2.2" fill="none"/></svg>

<!-- why choose us -->
<h2 class="abs section-title" style="top:2935px">Why <span class="accent">Parents Choose Us</span></h2>
<div class="abs reasons">
  <div class="reason">
    <svg viewBox="0 0 54 50" width="54" fill="#555"><circle cx="27" cy="14" r="8"/><circle cx="11" cy="18" r="6"/><circle cx="43" cy="18" r="6"/><path d="M14 44c0-10 6-16 13-16s13 6 13 16z"/><path d="M1 42c0-8 4-13 10-13 3 0 5 1 6 2-3 3-5 7-5 11z"/><path d="M53 42c0-8-4-13-10-13-3 0-5 1-6 2 3 3 5 7 5 11z"/></svg>
    <p>Small groups &amp; personalized attention</p>
  </div>
  <div class="reason">
    <svg viewBox="0 0 54 50" width="54" fill="none" stroke="#555" stroke-width="3"><path d="M27 8l22 9-22 9-22-9z" fill="#555"/><path d="M5 25l22 9 22-9M5 33l22 9 22-9"/></svg>
    <p>High-quality fabrics &amp; top-quality sewing machines (Elvara)</p>
  </div>
  <div class="reason">
    <svg viewBox="0 0 54 50" width="54" fill="none" stroke="#555" stroke-width="3"><path d="M27 10a11 11 0 0 0-7 19v6h14v-6a11 11 0 0 0-7-19z" fill="#555"/><path d="M21 40h12M23 45h8M27 2v3M9 10l3 2M45 10l-3 2M4 24h4M46 24h4"/></svg>
    <p>Encouragement of creativity, self-confidence, and fine motor skills</p>
  </div>
  <div class="reason">
    <svg viewBox="0 0 54 50" width="54" fill="#555"><path d="M27 4a21 21 0 0 1 18 10l-7 4a13 13 0 0 0-11-6z"/><path d="M47 20a21 21 0 0 1-3 21l-6-5a13 13 0 0 0 2-12z"/><path d="M38 44a21 21 0 0 1-27-6l7-4a13 13 0 0 0 16 4z"/><path d="M8 34a21 21 0 0 1 8-26l4 7a13 13 0 0 0-5 15z"/></svg>
    <p>Safe, loving environment in Zurich, various places easy to reach</p>
  </div>
  <div class="reason">
    <svg viewBox="0 0 54 50" width="54" fill="#555"><circle cx="30" cy="8" r="6"/><path d="M24 16h12v18l-4 14h-6l2-14h-4z"/><rect x="10" y="22" width="14" height="14"/><path d="M36 18l8 8-3 3-5-5z"/></svg>
    <p>Pick-up Service from the Main-Station</p>
  </div>
  <div class="reason">
    <svg viewBox="0 0 54 50" width="54" fill="none" stroke="#555" stroke-width="3"><rect x="6" y="4" width="24" height="26" fill="#555"/><rect x="24" y="18" width="24" height="26" fill="#fff"/><path d="M30 26h12M36 24v3M32 38c4-2 7-6 8-11M34 30c2 4 5 7 8 8"/></svg>
    <p>Multilingual supervision (DE / EN / IT)</p>
  </div>
</div>

<!-- faq band -->
<section class="abs band" style="top:3346px">
  <div class="side" role="img" aria-label="Two girls crafting with red pipe cleaners outdoors" style="background:linear-gradient(135deg,#c9b9a3,#d27a62 55%,#9b4a3c)"></div>
  <div class="mid" style="background:var(--teal)">
    <h2 style="position:absolute;left:0;width:100%;top:54px">Frequently<br>Asked<br>Questions</h2>
    <p style="position:absolute;left:40px;width:266px;top:234px;font-family:'Signika',sans-serif;font-size:22px;line-height:37px">Does my child need any prior knowledge?</p>
    <div class="btn coral" style="left:116px;top:337px;width:115px;height:44px;font-size:15px">View All</div>
  </div>
  <div class="side" role="img" aria-label="Children weaving colourful yarn crafts at a fair" style="background:linear-gradient(135deg,#6a7f8c,#c88b6b 55%,#a33f3a)"></div>
</section>

<!-- footer -->
<footer class="abs footer"></footer>
<div class="abs f-brand"><span>Tiny-ThreadDays</span><span class="dot"></span></div>
<div class="abs socials"><span></span><span></span><span></span><span></span><span></span></div>

<div class="abs f-head" style="left:393px;top:3936px">Quick Links</div>
<div class="abs links">Home<br>About Us<br>Camp<br>How It Works<br>Why Choose Us<br>Blog<br>Contact Us</div>

<div class="abs f-head" style="left:580px;top:3936px">Contact Info</div>
<div class="contact-row" style="top:3988px">
  <svg width="22" height="22" viewBox="0 0 22 22"><circle cx="11" cy="11" r="11" fill="#fff"/><path d="M11 4.5a4.5 4.5 0 0 0-4.5 4.5c0 3.5 4.5 8.5 4.5 8.5s4.5-5 4.5-8.5A4.5 4.5 0 0 0 11 4.5z" fill="#0c0c0c"/><circle cx="11" cy="9" r="1.6" fill="#fff"/></svg>
  <span>Lorem Ipsum, USA -437916</span>
</div>
<div class="contact-row" style="top:4046px">
  <svg width="22" height="22" viewBox="0 0 22 22"><circle cx="11" cy="11" r="11" fill="#fff"/><path d="M7 6l2.5-.5 1.5 3-1.5 1c.7 1.6 1.6 2.5 3 3l1-1.5 3 1.5-.5 2.5c-4.5.5-9-4-9-9z" fill="#0c0c0c"/></svg>
  <span>+41 44 555 01 23</span>
</div>
<div class="contact-row" style="top:4104px">
  <svg width="22" height="22" viewBox="0 0 22 22"><circle cx="11" cy="11" r="11" fill="#fff"/><rect x="5.5" y="7" width="11" height="8" rx="1" fill="#0c0c0c"/><path d="M6 8l5 4 5-4" stroke="#fff" stroke-width="1.2" fill="none"/></svg>
  <span>info@tiny-threaddays.ch</span>
</div>

<div class="abs f-head" style="left:854px;top:3936px">Our Newsletter</div>
<p class="abs news-text">Join our mailing list for special offers, news &amp; parenting tips right in your inbox.</p>
<div class="abs email-field">Enter email address</div>
<div class="btn coral" style="left:854px;top:4122px;width:117px;height:43px;font-size:16px">Subscribe</div>

<div class="abs rule"></div>
<p class="abs copy">© 2025 Tiny-ThreadDays .All rights reserved</p>

</body>
</html>
```